verdant terraces simple classy business card design

my name is colin barrow and I run a gardening business aimed at high class verdant terraces. the business name is verdant terraces and our logo was designed on pixel harbour .My clientel are anything from residential homes to businesses. I take pride in my work and know that I offer a service like no other in my area.
The business card will be used to represent my business and I want it to be not only rememberable, but simplistic and modern. Eye catching too. Of course I would like it relatable to gardening and appealing to the correct clientel - those being garden enthusiasts, prestigious homes and businesses that are after top of the line gardening services like no other on the market.
I am not a typical lawn mowing business so I don't want a typical card design that represents that. The gardens I work with are generally million dollar properties with owners who are very garden proud looking for upkeep and guidance from me along with sometimes whole new garden designs. I want the business cards to show to my clients that I take pride, as they do, in their garden. And I want them to know from my card that I am a professional, qualified horticulturist offering them a top of the line service for life. I want them to refer my business on. I want them to look at my business card and see class and professionalism in a modern unique bold way.
The card should be simple with the possibility of the logo on the front being embossed/debossed and my details on the back the card should have a organic garden feel it's very important to me that it is absolutely perfect
I am also very open to ideas and suggestions so look forward to seeing the designs. the business logo has been supplied with this project and I want the card to be double sided

Contact info is
Colin Barrow - Managing Director / Horticulturist
Phone : 0481 526 704
Email: colinbarrow@verdantterraces.example.au

Target Market(s)

high class gardens residential and commercial

Industry/Entity Type

Gardener

Contact Information for Business Card

Contact info is
Phone : 0481 526 704

PLEASE MAKE CARD DOUBLE SIDED

Requirements
Must have
• organic simple classy modern feel
• must flow with the current logo that has been supplied with this project
• Double sided
• Must explain in a simple way that I deal with high end gardens and I'm a qualified horticulturist
Nice to have
• embossed debossed logo
Should not have
• shouldn't be to busy or cheap looking

```html
<!DOCTYPE html>
<html lang="en">
<head>
<meta charset="utf-8">
<title>Verdant Terraces – Business Card</title>
<link href="https://fonts.googleapis.com/css2?family=Tinos:wght@400;700&family=Open+Sans:wght@400&display=swap" rel="stylesheet">
<style>
  :root {
    --backdrop: #ecebe8;
    --card-white: #ffffff;
    --garden-green: #5a9a4e;
    --ink: #1e1e1e;
    --reverse-text: #ffffff;
  }
  html, body {
    margin: 0;
    padding: 0;
    width: 1200px;
    height: 900px;
    overflow: hidden;
    background: var(--backdrop);
  }
  .canvas {
    position: relative;
    width: 1200px;
    height: 900px;
  }
  .card {
    position: absolute;
    box-sizing: border-box;
    box-shadow: 0 6px 18px rgba(0,0,0,0.12);
    overflow: hidden;
  }
  .brand {
    position: absolute;
    left: 0;
    right: 0;
    text-align: center;
    font-family: "Tinos", "Times New Roman", serif;
    font-weight: 400;
    color: var(--garden-green);
    text-transform: uppercase;
    line-height: 1;
  }
  .brand__mark {
    display: block;
    margin: 0 auto 14px;
    width: 88px;
    height: 88px;
    border-radius: 50%;
    background: var(--garden-green);
  }
  .brand__name-main {
    display: block;
    font-size: 46px;
    letter-spacing: 1px;
  }
  .brand__name-sub {
    display: block;
    margin-top: 6px;
    padding-left: 14px;
    font-size: 26px;
    letter-spacing: 14px;
  }

  /* Details side */
  .card--details {
    left: 78px;
    top: 35px;
    width: 588px;
    height: 362px;
    background: var(--card-white);
  }
  .card--details .brand { top: 34px; }
  .person {
    position: absolute;
    left: 40px;
    top: 232px;
    width: 190px;
    text-align: right;
  }
  .person__name {
    margin: 0;
    font-family: "Tinos", "Times New Roman", serif;
    font-weight: 700;
    font-size: 23px;
    line-height: 26px;
    color: var(--garden-green);
  }
  .person__role {
    margin: 2px 0 0;
    font-family: "Open Sans", Arial, sans-serif;
    font-size: 14px;
    line-height: 18px;
    color: var(--ink);
  }
  .contact {
    position: absolute;
    left: 246px;
    top: 233px;
    margin: 0;
    padding: 0;
    list-style: none;
    font-family: "Open Sans", Arial, sans-serif;
    font-size: 14px;
    color: var(--ink);
  }
  .contact__item {
    display: flex;
    align-items: center;
    height: 21px;
    white-space: nowrap;
  }
  .contact__icon {
    flex: none;
    width: 12px;
    height: 12px;
    margin-right: 12px;
    fill: var(--garden-green);
  }
  .contact__icon--line {
    fill: none;
    stroke: var(--garden-green);
    stroke-width: 1.1;
  }
  .tagline {
    position: absolute;
    left: 0;
    right: 0;
    top: 311px;
    margin: 0;
    text-align: center;
    font-family: "Open Sans", Arial, sans-serif;
    font-size: 15px;
    color: var(--ink);
  }

  /* Logo side */
  .card--logo {
    left: 388px;
    top: 505px;
    width: 567px;
    height: 352px;
    background: var(--garden-green);
  }
  .card--logo .brand {
    top: 98px;
    color: var(--reverse-text);
  }
  .card--logo .brand__mark {
    background: var(--reverse-text);
    width: 94px;
    height: 94px;
    margin-bottom: 12px;
  }
  .card--logo .brand__name-main { font-size: 40px; }
  .card--logo .brand__name-sub { font-size: 22px; letter-spacing: 13px; padding-left: 13px; }
</style>
</head>
<body>
<main class="canvas">

  <section class="card card--details" aria-label="Business card, details side">
    <div class="brand">
      <span class="brand__mark" aria-hidden="true"></span>
      <span class="brand__name-main">Verdant</span>
      <span class="brand__name-sub">Terraces</span>
    </div>

    <div class="person">
      <p class="person__name">Colin Barrow</p>
      <p class="person__role">Managing Director</p>
      <p class="person__role">Qualified Horticulturist</p>
    </div>

    <ul class="contact">
      <li class="contact__item">
        <svg class="contact__icon" viewBox="0 0 12 12" aria-hidden="true"><path d="M2.4 0.6 L4.2 2.8 L3.2 4.2 C3.9 5.7 5.5 7.4 7.6 8.6 L8.9 7.6 L11.2 9.4 L10 11.4 C5.2 11.2 0.6 6.6 0.5 1.8 Z"/></svg>
        <span>0481 526 704</span>
      </li>
      <li class="contact__item">
        <svg class="contact__icon" viewBox="0 0 12 12" aria-hidden="true"><path d="M1 2.5 H11 V9.5 H1 Z M1.6 3 L6 6.6 L10.4 3 Z" fill-rule="evenodd"/></svg>
        <span>colinbarrow@verdantterraces.example.au</span>
      </li>
      <li class="contact__item">
        <svg class="contact__icon contact__icon--line" viewBox="0 0 12 12" aria-hidden="true"><circle cx="6" cy="6" r="5.2"/><path d="M0.8 6 H11.2 M6 0.8 C3.6 3.4 3.6 8.6 6 11.2 M6 0.8 C8.4 3.4 8.4 8.6 6 11.2"/></svg>
        <span>www.verdantterraces.example.au</span>
      </li>
    </ul>

    <p class="tagline">High-End Residential &amp; Commercial Gardens</p>
  </section>

  <section class="card card--logo" aria-label="Business card, logo side">
    <div class="brand">
      <span class="brand__mark" aria-hidden="true"></span>
      <span class="brand__name-main">Verdant</span>
      <span class="brand__name-sub">Terraces</span>
    </div>
  </section>

</main>
</body>
</html>
```